redesign of my existing custom website into Wordpress based website

I need someone to redesign my current website into something more classy, simplistic, modern and on trend. I would like it set up on Wordpress in a way thats easy for me to make my own additions to blogs/price changes and promotion banners. I will also need a page that is password protected so members can login and have access to all my training videos and resources.
website is www.tidewellmamas.com.au

Target Market(s)

new mums

Industry/Entity Type

Fitness

Coding

Coded - Design and coding required

Number of Pages Required

5+ page

Colors
33a6d7

Requirements
Must have
• chic, modern, stylish and simplistic.
• a call to action above the page fold
• mobile friendly conversion
• a pop up message as soon as someone enters my sight offering my free report
• a members page that is password protected containing 3 youtube videos and 6 pdf attachments as resources
• a home page
• a contact us page
• an about us page
• a blog page
• a store page
Nice to have
• some examples of my peers websites that I like:
• www.norapellwick.com
• https://www.9qlr.com
• https://41bytedgarth.com
Should not have
• anything gimmicky

```html
<!DOCTYPE html>
<html lang="en">
<head>
<meta charset="utf-8">
<title>Tidewell Mamas – 12 Week Challenge</title>
<link href="https://fonts.googleapis.com/css2?family=Lato:ital,wght@0,400;0,700;0,900;1,400;1,700;1,900&family=Open+Sans:wght@400;600;700&display=swap" rel="stylesheet">
<style>
:root{
  --pink:#ec1a72;
  --pink-dark:#d0105f;
  --ink:#2b2b2b;
  --text:#555a60;
  --muted:#8b9096;
  --light:#eef0f4;
  --pale:#f6f7fa;
  --white:#ffffff;
  --hero-dark:#3b3f45;
  --hero-mid:#4d5259;
}
*{box-sizing:border-box;margin:0;padding:0}
html,body{width:1200px;height:3930px;overflow:hidden}
body{font-family:'Open Sans',Arial,sans-serif;color:var(--text);background:var(--white);position:relative}
h1,h2,h3,h4{font-family:'Lato',Helvetica,sans-serif;color:var(--ink)}
.btn{display:inline-flex;align-items:center;justify-content:center;gap:8px;height:52px;padding:0 34px;border-radius:26px;background:var(--pink);color:var(--white);font-family:'Lato',sans-serif;font-weight:700;font-size:16px;letter-spacing:.5px;text-transform:uppercase;text-decoration:none}
.btn--ghost{background:transparent;border:2px solid rgba(255,255,255,.8)}
section,footer.site-footer{position:absolute;left:0;width:1200px;overflow:hidden}

/* header */
.site-header{top:0;height:92px;border-top:4px solid var(--pink);border-bottom:3px solid var(--pink);background:var(--white)}
.brand{position:absolute;left:100px;top:14px;display:flex;align-items:center;gap:10px;font-family:'Lato',sans-serif;font-weight:700;font-size:20px;color:var(--ink)}
.brand__dot{width:52px;height:52px;border-radius:50%;border:3px solid var(--ink);flex:none}
.main-nav{position:absolute;right:100px;top:26px;display:flex;align-items:center;gap:34px;font-family:'Lato',sans-serif;font-weight:700;font-size:15px;color:var(--ink)}
.main-nav .is-active{color:var(--pink)}
.nav-login{display:flex;align-items:center;gap:6px;height:36px;padding:0 20px;border:1.5px solid #c9ccd1;border-radius:18px}
.nav-join{height:36px;padding:0 28px;border-radius:18px;background:var(--pink);color:var(--white);display:flex;align-items:center}

/* hero */
.hero{top:92px;height:490px;background:radial-gradient(ellipse at 35% 40%,var(--hero-mid),var(--hero-dark) 75%)}
.hero__photo{position:absolute;right:0;top:0;width:460px;height:490px;background:linear-gradient(180deg,#6a6c70,#8a7560 45%,#b9927a)}
.hero__text{position:absolute;left:100px;top:110px;width:620px;color:var(--white)}
.hero__lead{font-family:'Lato',sans-serif;font-style:italic;font-size:24px;color:var(--white)}
.hero h1{color:var(--white);font-size:40px;font-weight:700;line-height:1.25;margin:14px 0 12px}
.hero__sub{font-family:'Lato',sans-serif;font-size:22px}
.hero__actions{display:flex;gap:26px;margin-top:40px}
.hero__actions .btn{height:50px;width:168px;padding:0}

/* tips */
.tips{top:582px;height:204px;background:var(--light)}
.tips__kicker{position:absolute;left:96px;top:36px;font-family:'Lato',sans-serif;font-weight:700;font-size:22px;color:var(--pink)}
.tips__copy{position:absolute;left:96px;top:76px;font-size:17px;color:var(--ink)}
.tips__title{position:absolute;left:96px;top:108px;font-size:38px;font-style:italic;font-weight:900}
.tips .btn{position:absolute;left:878px;top:76px;width:228px;height:54px;padding:0}

/* why */
.why{top:786px;height:524px}
.why h2{position:absolute;left:96px;top:60px;width:460px;font-size:30px;line-height:1.3;font-weight:700}
.checklist{position:absolute;left:96px;top:168px;width:440px;list-style:none}
.checklist li{position:relative;padding-left:34px;margin-bottom:20px;font-size:14px;line-height:1.55;color:var(--text)}
.checklist li svg{position:absolute;left:0;top:2px}
.why__video{position:absolute;left:606px;top:130px;width:494px;height:300px;background:linear-gradient(135deg,#2e2a28,#5a4a42 55%,#3a3532)}
.play{position:absolute;left:217px;top:120px}

/* cta */
.cta{top:1310px;height:275px;background:linear-gradient(90deg,#dedfe2,#ecebed 50%,#d8d5d8)}
.cta::before{content:"";position:absolute;inset:0;background:rgba(255,255,255,.55)}
.cta__inner{position:relative;text-align:center;padding-top:55px}
.cta h2{font-size:30px;font-weight:700}
.cta h2 u{text-underline-offset:4px}
.cta p{margin:18px 0 34px;font-size:17px;color:var(--ink)}
.cta .btn{width:228px;padding:0}

/* results */
.results{top:1585px;height:590px;background:linear-gradient(160deg,#4a4a4c,#2e2d2f 60%,#3a3838)}
.results::before{content:"";position:absolute;inset:0;background:rgba(0,0,0,.35)}
.results h2{position:relative;text-align:center;color:var(--white);font-size:30px;font-weight:700;line-height:1.35;padding-top:50px}
.result-cards{position:absolute;left:100px;top:175px;display:flex;gap:25px}
.result-card{width:232px;height:362px;background:var(--white);box-shadow:0 4px 14px rgba(0,0,0,.3)}
.result-card__photo{height:170px;display:flex;gap:4px;padding:4px 4px 0}
.result-card__photo div{flex:1;background:linear-gradient(180deg,#9b8a80,#c7a58f)}
.result-card__body{text-align:center;padding:14px 14px 0}
.result-card h3{font-size:16px;font-weight:700}
.result-card .result-card__role{font-size:11px;color:var(--muted)}
.result-card .result-card__stat{font-family:'Lato',sans-serif;font-weight:700;font-size:16px;color:var(--pink);line-height:1.3;margin:6px 0}
.result-card__quote{font-size:10.5px;line-height:1.5;color:var(--text)}

/* included */
.included{top:2175px;height:600px}
.included__media{position:absolute;left:96px;top:95px;width:494px;height:330px;background:linear-gradient(90deg,#6c5a52,#d95f8f 45%,#e8c8a8 70%,#4d4e56)}
.included h2{position:absolute;left:652px;top:85px;font-size:30px;font-weight:700}
.included .checklist{left:652px;top:150px;width:450px}
.included .checklist li{margin-bottom:16px}
.price{position:absolute;left:652px;top:435px;font-family:'Lato',sans-serif;font-weight:700;font-size:16px;color:var(--ink)}
.price small{display:block;font-family:'Open Sans',sans-serif;font-weight:400;font-size:11px;color:var(--muted);margin-top:4px}
.included .btn{position:absolute;left:652px;top:490px;width:228px;padding:0}

/* news */
.news{top:2775px;height:555px;background:var(--pale)}
.news h2{text-align:center;font-size:30px;font-weight:700;padding-top:50px}
.news-grid{position:absolute;left:96px;top:130px;display:flex;gap:26px}
.news-card{width:232px;height:356px;background:var(--white);box-shadow:0 2px 8px rgba(0,0,0,.08);text-align:center}
.news-card__img{height:172px}
.news-card h3{font-size:14px;font-weight:700;line-height:1.4;padding:20px 16px 8px}
.news-card p{font-size:11px;line-height:1.55;color:var(--muted);padding:0 22px}
.news-card__meta{display:flex;justify-content:center;gap:18px;margin-top:16px;font-family:'Lato',sans-serif;font-weight:700;font-size:13px;color:var(--pink)}
.news-card__meta span{display:flex;align-items:center;gap:4px}

/* quote */
.quote{top:3330px;height:285px;background:var(--pink)}
.quote__photo{position:absolute;left:0;top:0;width:320px;height:285px;background:linear-gradient(135deg,#c6b8ac,#e5d8cc 50%,#a99384)}
.quote blockquote{position:absolute;left:365px;top:38px;width:740px;color:var(--white);font-family:'Lato',sans-serif;font-style:italic;font-weight:700;font-size:15.5px;line-height:1.75}
.quote cite{position:absolute;left:365px;top:218px;color:var(--white);font-family:'Lato',sans-serif;font-style:normal;font-weight:700;font-size:20px}

/* footer */
.site-footer{top:3615px;height:315px;background:var(--white)}
.footer-brand{position:absolute;left:96px;top:60px;display:flex;align-items:center;gap:12px;font-family:'Lato',sans-serif;font-weight:700;font-size:22px;color:var(--ink)}
.footer-brand .brand__dot{width:72px;height:72px}
.footer-col{position:absolute;top:40px}
.footer-col h4{font-size:18px;font-weight:700;margin-bottom:12px}
.footer-col ul{list-style:none}
.footer-col li{font-size:13px;line-height:1.75;color:var(--text)}
.footer-col p{font-size:13px;line-height:1.6;width:260px;color:var(--text)}
.footer-col .btn{height:38px;padding:0 22px;font-size:12px;margin-top:14px}
.social{display:flex;align-items:center;gap:14px;margin-bottom:18px;font-size:13px}
.social i{width:30px;height:30px;background:#6d7177;border-radius:3px;display:block}
.copyright{position:absolute;left:96px;right:96px;top:262px;border-top:1px solid #dde0e4;padding-top:14px;text-align:center;font-size:11px;color:var(--muted)}
</style>
</head>
<body>

<section class="site-header">
  <div class="brand"><span class="brand__dot"></span>Tidewell Mamas</div>
  <nav class="main-nav">
    <span class="is-active">HOME</span><span>ABOUT US</span><span>PROGRAM</span><span>BLOG</span><span>FAQ</span><span>CONTACT</span>
    <span class="nav-login"><svg width="12" height="14" viewBox="0 0 12 14"><rect x="1" y="6" width="10" height="8" rx="1" fill="#ec1a72"/><path d="M3 6V4a3 3 0 0 1 6 0v2" stroke="#ec1a72" stroke-width="1.6" fill="none"/></svg>LOGIN</span>
    <span class="nav-join">JOIN</span>
  </nav>
</section>

<section class="hero">
  <div class="hero__photo" role="img" aria-label="Smiling fitness coach in a grey top against a dark wall"></div>
  <div class="hero__text">
    <p class="hero__lead">Transform your body and mind in just 12 weeks with my</p>
    <h1>Tidewell Mamas 12 week<br>Challenge</h1>
    <p class="hero__sub">and do it from the comfort of your own home</p>
    <div class="hero__actions">
      <span class="btn">Learn more <svg width="14" height="14" viewBox="0 0 14 14"><circle cx="7" cy="7" r="6" fill="#fff"/><path d="M6 4l3 3-3 3" stroke="#ec1a72" stroke-width="1.6" fill="none"/></svg></span>
      <span class="btn btn--ghost">Join now</span>
    </div>
  </div>
</section>

<section class="tips">
  <p class="tips__kicker">Bounce Back into a Fitter, Healthier, More Energetic you!</p>
  <p class="tips__copy">Let me share with you some of my best secrets to bouncing back after baby with my FREE</p>
  <h2 class="tips__title">Top 10 Bouncing Back Tips</h2>
  <span class="btn">Get it free now!</span>
</section>

<section class="why">
  <h2>Why choose the Tidewell Mamas 12 Week Challenge</h2>
  <ul class="checklist">
    <li><svg width="18" height="18" viewBox="0 0 18 18"><circle cx="9" cy="9" r="9" fill="#ec1a72"/><path d="M5 9.5l2.6 2.5L13 6.5" stroke="#fff" stroke-width="2" fill="none"/></svg>A program uniquely tailored to suit bodies post pregnancy</li>
    <li><svg width="18" height="18" viewBox="0 0 18 18"><circle cx="9" cy="9" r="9" fill="#ec1a72"/><path d="M5 9.5l2.6 2.5L13 6.5" stroke="#fff" stroke-width="2" fill="none"/></svg>A workout program that grows with you as your fitness and strength improve</li>
    <li><svg width="18" height="18" viewBox="0 0 18 18"><circle cx="9" cy="9" r="9" fill="#ec1a72"/><path d="M5 9.5l2.6 2.5L13 6.5" stroke="#fff" stroke-width="2" fill="none"/></svg>Proven training methods built by a post pregnancy specialist trainer and mum</li>
    <li><svg width="18" height="18" viewBox="0 0 18 18"><circle cx="9" cy="9" r="9" fill="#ec1a72"/><path d="M5 9.5l2.6 2.5L13 6.5" stroke="#fff" stroke-width="2" fill="none"/></svg>A dedicated focus on rebuilding core strength</li>
    <li><svg width="18" height="18" viewBox="0 0 18 18"><circle cx="9" cy="9" r="9" fill="#ec1a72"/><path d="M5 9.5l2.6 2.5L13 6.5" stroke="#fff" stroke-width="2" fill="none"/></svg>Delicious and healthy family friendly recipes</li>
    <li><svg width="18" height="18" viewBox="0 0 18 18"><circle cx="9" cy="9" r="9" fill="#ec1a72"/><path d="M5 9.5l2.6 2.5L13 6.5" stroke="#fff" stroke-width="2" fill="none"/></svg>The ultimate convenience of being able to train from home, anytime you want!</li>
  </ul>
  <div class="why__video" role="img" aria-label="Video still of a mum doing a plank exercise beside her baby in a lounge room">
    <svg class="play" width="60" height="60" viewBox="0 0 60 60"><circle cx="30" cy="30" r="29" fill="rgba(255,255,255,.85)"/><path d="M24 18l18 12-18 12z" fill="#333"/></svg>
  </div>
</section>

<section class="cta" role="img" aria-label="Faded background of a woman training in a gym">
  <div class="cta__inner">
    <h2>Don’t waste anymore time <u>Thinking</u> about getting back into shape</h2>
    <p>Take the first step to a fitter healthier more energetic you and join our program today!</p>
    <span class="btn">Get started now!</span>
  </div>
</section>

<section class="results" role="img" aria-label="Dark blurred gym background">
  <h2>Check out some of the awesome results already<br>achieved by mums on our challenge</h2>
  <div class="result-cards">
    <article class="result-card">
      <div class="result-card__photo" role="img" aria-label="Before and after photos of Mara"><div></div><div></div></div>
      <div class="result-card__body">
        <h3>Mara</h3>
        <p class="result-card__role">Tidewell Mamas Founder</p>
        <p class="result-card__stat">Lost 15kgs and 25cms<br>in 12 weeks</p>
        <p class="result-card__quote">This is the exact program I used after 2 of my babies and I lost around 15kg in 12 weeks both times.</p>
      </div>
    </article>
    <article class="result-card">
      <div class="result-card__photo" role="img" aria-label="Before and after photos of Jessa"><div></div><div></div></div>
      <div class="result-card__body">
        <h3>Jessa</h3>
        <p class="result-card__stat">Lost 10kgs in 12<br>weeks</p>
        <p class="result-card__quote">Its rare a program delivers what it promises and everyone should know yours is the real deal!</p>
      </div>
    </article>
    <article class="result-card">
      <div class="result-card__photo" role="img" aria-label="Before and after photos of Coralie"><div></div><div></div></div>
      <div class="result-card__body">
        <h3>Coralie</h3>
        <p class="result-card__stat">Lost 20cms in 12 weeks</p>
        <p class="result-card__quote">I am really happy with my results, I have lost 20cms across my body and lost 8kg, but most importantly my flabby tummy is gone and I feel toned all over.</p>
      </div>
    </article>
    <article class="result-card">
      <div class="result-card__photo" role="img" aria-label="Before and after photos of RB"><div></div><div></div></div>
      <div class="result-card__body">
        <h3>RB</h3>
        <p class="result-card__stat">Lost 18cms in 12 weeks</p>
        <p class="result-card__quote">This program was exactly what I needed! Within a matter of months I was back in my old clothes and had people commenting about how quickly I had bounced back.</p>
      </div>
    </article>
  </div>
</section>

<section class="included">
  <div class="included__media" role="img" aria-label="Collage of a trainer with dumbbells, the healthy eating guide cover and a plated meal"></div>
  <h2>What’s included in the program?</h2>
  <ul class="checklist">
    <li><svg width="18" height="18" viewBox="0 0 18 18"><circle cx="9" cy="9" r="9" fill="#ec1a72"/><path d="M5 9.5l2.6 2.5L13 6.5" stroke="#fff" stroke-width="2" fill="none"/></svg>Our unique 3 stage, cardio, resistance and core, 12 week training program</li>
    <li><svg width="18" height="18" viewBox="0 0 18 18"><circle cx="9" cy="9" r="9" fill="#ec1a72"/><path d="M5 9.5l2.6 2.5L13 6.5" stroke="#fff" stroke-width="2" fill="none"/></svg>Full instructional online workout videos and program cards for each program</li>
    <li><svg width="18" height="18" viewBox="0 0 18 18"><circle cx="9" cy="9" r="9" fill="#ec1a72"/><path d="M5 9.5l2.6 2.5L13 6.5" stroke="#fff" stroke-width="2" fill="none"/></svg>Weekly accountability charts</li>
    <li><svg width="18" height="18" viewBox="0 0 18 18"><circle cx="9" cy="9" r="9" fill="#ec1a72"/><path d="M5 9.5l2.6 2.5L13 6.5" stroke="#fff" stroke-width="2" fill="none"/></svg>Weekly coaching emails</li>
    <li><svg width="18" height="18" viewBox="0 0 18 18"><circle cx="9" cy="9" r="9" fill="#ec1a72"/><path d="M5 9.5l2.6 2.5L13 6.5" stroke="#fff" stroke-width="2" fill="none"/></svg>Nutritionist approved healthy eating guide</li>
    <li><svg width="18" height="18" viewBox="0 0 18 18"><circle cx="9" cy="9" r="9" fill="#ec1a72"/><path d="M5 9.5l2.6 2.5L13 6.5" stroke="#fff" stroke-width="2" fill="none"/></svg>Healthy Family Favourites recipe ebook</li>
  </ul>
  <p class="price">All for just $89<small>One time only payment</small></p>
  <span class="btn">Get started now!</span>
</section>

<section class="news">
  <h2>Top News</h2>
  <div class="news-grid">
    <article class="news-card">
      <div class="news-card__img" role="img" aria-label="Woman training with a step in a home gym" style="background:linear-gradient(135deg,#3c3a3e,#8a7e7a)"></div>
      <h3>The benefits of training in the morning</h3>
      <p>Cum soluta nobis est eligendi optio cumque nihil impedit quo minus id quod maxime placeat possimus...</p>
      <div class="news-card__meta"><span>JAN 02</span><span><svg width="12" height="11" viewBox="0 0 12 11"><path d="M6 11L1 6a3 3 0 0 1 5-4 3 3 0 0 1 5 4z" fill="#ec1a72"/></svg>21</span></div>
    </article>
    <article class="news-card">
      <div class="news-card__img" role="img" aria-label="Woman doing a cardio move in a lounge room" style="background:linear-gradient(135deg,#2f2b2c,#7a5a58)"></div>
      <h3>Mara’s 10 exercise lounge room cardio workout</h3>
      <p>Cum soluta nobis est eligendi optio cumque nihil impedit quo minus id quod maxime placeat possimus...</p>
      <div class="news-card__meta"><span>JAN 02</span><span><svg width="12" height="11" viewBox="0 0 12 11"><path d="M6 11L1 6a3 3 0 0 1 5-4 3 3 0 0 1 5 4z" fill="#ec1a72"/></svg>21</span></div>
    </article>
    <article class="news-card">
      <div class="news-card__img" role="img" aria-label="Golden shepherds pie pastries on a white plate" style="background:linear-gradient(135deg,#c9c6c0,#e8c070)"></div>
      <h3>Healthy Shepherds Pie Recipe</h3>
      <p>Cum soluta nobis est eligendi optio cumque nihil impedit quo minus id quod maxime placeat possimus...</p>
      <div class="news-card__meta"><span>JAN 02</span><span><svg width="12" height="11" viewBox="0 0 12 11"><path d="M6 11L1 6a3 3 0 0 1 5-4 3 3 0 0 1 5 4z" fill="#ec1a72"/></svg>21</span></div>
    </article>
    <article class="news-card">
      <div class="news-card__img" role="img" aria-label="Baked sweet treats on a dark wooden table" style="background:linear-gradient(135deg,#3a2a22,#c06a38)"></div>
      <h3>Dairy, Gluten, Sugar, Guilt Free Easter the morning</h3>
      <p>Cum soluta nobis est eligendi optio cumque nihil impedit quo minus id quod maxime placeat possimus...</p>
      <div class="news-card__meta"><span>JAN 02</span><span><svg width="12" height="11" viewBox="0 0 12 11"><path d="M6 11L1 6a3 3 0 0 1 5-4 3 3 0 0 1 5 4z" fill="#ec1a72"/></svg>21</span></div>
    </article>
  </div>
</section>

<section class="quote">
  <div class="quote__photo" role="img" aria-label="Mum cuddling her baby at home"></div>
  <blockquote>As a mother of 3 beautiful babies I know exactly how hard it can be to find the time and energy to focus on yourself. That’s why I designed a program that was easy to follow, could fit into the life of a busy mum and was focused on all the areas that need attention after babies. I’m so passionate about sharing what I have learnt through all my post pregnancy training courses and time spent with physio’s and hope I can also help you to become a fitter, healthier more energetic you!</blockquote>
  <cite>- Mara Ellison</cite>
</section>

<footer class="site-footer">
  <div class="footer-brand"><span class="brand__dot"></span>Tidewell Mamas</div>
  <div class="footer-col" style="left:380px">
    <h4>Quick Links</h4>
    <ul><li>Home</li><li>About Us</li><li>Program</li><li>Blog</li><li>Shop</li><li>Contact Us</li></ul>
  </div>
  <div class="footer-col" style="left:555px">
    <h4>Subscribe</h4>
    <p>Register your details below and receive tones of free information on fitness and living a healthy lifestyle</p>
    <span class="btn">Subscribe</span>
  </div>
  <div class="footer-col" style="left:890px">
    <h4>Stay Connected</h4>
    <div class="social"><i></i>Kinnect</div>
    <div class="social"><i></i>Snapfold</div>
  </div>
  <p class="copyright">Copyrights © 2017. Tidewell Mamas. All rights reserved.</p>
</footer>

</body>
</html>
```